Business Cards for a law firm

Business cards for our law firm. Use our silhoette logo and OAK PARTNERS - check our website (www.oakpartners.example)

Contact Information for Business Card

our silhouette logo, OAK PARTNERS, 800-555-0147, Dorian Pemberton, dorian@oakpartners.example

Requirements
Must have
• our silhouette logo, OAK PARTNERS, 800-555-0147, Dorian Pemberton, dorian@oakpartners.example

```html
<!DOCTYPE html>
<html lang="en">
<head>
<meta charset="utf-8">
<title>Oak Partners — Business Cards</title>
<link rel="stylesheet" href="https://fonts.googleapis.com/css2?family=Open+Sans:wght@400;600;700&display=swap">
<style>
  :root {
    --backdrop: #e4e4e4;
    --paper: #ffffff;
    --navy: #00149c;
    --red: #ff0000;
    --ink: #1a1a1a;
  }
  * { margin: 0; padding: 0; box-sizing: border-box; }
  html, body { width: 1200px; height: 1200px; overflow: hidden; }
  body { background: var(--backdrop); font-family: "Open Sans", sans-serif; position: relative; }

  .card { position: absolute; left: 223px; width: 761px; background: var(--paper); overflow: hidden; }
  .card--front { top: 151px; height: 435px; }
  .card--back { top: 621px; height: 436px; }
  .card__shapes { position: absolute; inset: 0; width: 100%; height: 100%; }

  .brand { position: absolute; display: flex; align-items: center; font-weight: 700; letter-spacing: 0.04em; white-space: nowrap; }
  .brand__mark { display: block; }
  .brand--front { left: 0; width: 294px; top: 150px; flex-direction: column; gap: 22px; color: var(--paper); font-size: 23px; }
  .brand--front .brand__mark { width: 56px; height: 56px; background: var(--paper); }
  .brand--back { left: 0; right: 0; top: 178px; justify-content: center; gap: 22px; color: var(--navy); font-size: 46px; }
  .brand--back .brand__mark { width: 58px; height: 58px; background: var(--navy); }

  .person { position: absolute; left: 320px; top: 92px; color: var(--red); font-weight: 600; font-size: 41px; line-height: 1; letter-spacing: 0.005em; }

  .contacts { position: absolute; left: 320px; top: 206px; list-style: none; }
  .contacts__item { display: flex; align-items: center; height: 24px; margin-bottom: 12.5px; color: var(--ink); font-size: 19px; }
  .contacts__item:nth-child(3) { margin-bottom: 16px; }
  .contacts__icon { width: 23px; height: 23px; margin-right: 10px; flex: none; fill: var(--red); }
</style>
</head>
<body>

<section class="card card--front" aria-label="Card front">
  <svg class="card__shapes" viewBox="0 0 761 435" preserveAspectRatio="none" aria-hidden="true">
    <polygon points="0,0 294,0 294,435 221,344 0,344" fill="var(--navy)"/>
    <polygon points="0,361 198,361 264,435 0,435" fill="var(--red)"/>
  </svg>
  <div class="brand brand--front"><span class="brand__mark"></span><span>OAK PARTNERS</span></div>

  <h1 class="person">Dorian Pemberton</h1>

  <ul class="contacts">
    <li class="contacts__item">
      <svg class="contacts__icon" viewBox="0 0 24 24"><path d="M6.6 10.8a15.2 15.2 0 0 0 6.6 6.6l2.2-2.2a1 1 0 0 1 1-.25 11.4 11.4 0 0 0 3.6.57 1 1 0 0 1 1 1V20a1 1 0 0 1-1 1A17 17 0 0 1 3 4a1 1 0 0 1 1-1h3.5a1 1 0 0 1 1 1c0 1.25.2 2.45.57 3.57a1 1 0 0 1-.25 1z"/></svg>
      800-555-0147
    </li>
    <li class="contacts__item">
      <svg class="contacts__icon" viewBox="0 0 24 24"><rect x="1" y="4" width="22" height="16" rx="2.5"/><polyline points="4,7.5 12,13.5 20,7.5" fill="none" stroke="#fff" stroke-width="2"/></svg>
      dorian@oakpartners.example
    </li>
    <li class="contacts__item">
      <svg class="contacts__icon" viewBox="0 0 24 24"><circle cx="12" cy="12" r="10.5"/><g fill="none" stroke="#fff" stroke-width="1.5"><line x1="1.5" y1="12" x2="22.5" y2="12"/><line x1="12" y1="1.5" x2="12" y2="22.5"/><line x1="3" y1="7.5" x2="21" y2="7.5"/><line x1="3" y1="16.5" x2="21" y2="16.5"/><ellipse cx="12" cy="12" rx="5" ry="10.5"/></g></svg>
      Www.yourweb.com
    </li>
    <li class="contacts__item">
      <svg class="contacts__icon" viewBox="0 0 24 24"><path d="M12 1a8 8 0 0 0-8 8c0 5.5 8 14 8 14s8-8.5 8-14a8 8 0 0 0-8-8zm0 11a3 3 0 1 1 0-6 3 3 0 0 1 0 6z"/></svg>
      Your Street,City,State,Pin Code,Country
    </li>
  </ul>
</section>

<section class="card card--back" aria-label="Card back">
  <svg class="card__shapes" viewBox="0 0 761 436" preserveAspectRatio="none" aria-hidden="true">
    <polygon points="0,0 282,0 237,21 0,21" fill="var(--red)"/>
    <polygon points="164,436 226,404 563,404 498,436" fill="var(--red)"/>
    <polygon points="498,436 563,404 761,404 761,436" fill="var(--navy)"/>
  </svg>
  <div class="brand brand--back"><span class="brand__mark"></span><span>OAK PARTNERS</span></div>
</section>

</body>
</html>
```